Brisk Coatings business card for residential and commercial painting

A clean, professional design. Easy to read
Eye catching and elegant
Front could have some color variations
On the back of card I would like all black with signature logo

*Attached is my current business card and the items I want displayed

Contact Information for Business Card

Email, phone number, website, and owner name

Font styles to use
Serif

Requirements
Must have
• My logo with cool design and perhaps some paint splatter

```html
<!DOCTYPE html>
<html lang="en">
<head>
<meta charset="utf-8">
<title>Brisk Coatings Business Card</title>
<link rel="stylesheet" href="https://fonts.googleapis.com/css2?family=Open+Sans:wght@400;600;700&display=swap">
<style>
  :root {
    --backdrop: #6b6768;
    --card-dark: #333336;
    --card-light: #f7f7f5;
    --rule: #bdbdbd;
    --ink-deep: #19191a;
    --brand-blue: #1a70c6;
    --text-light: #f2f2f2;
    --art-tone-a: #55555a;
    --art-tone-b: #46464a;
  }
  * { box-sizing: border-box; margin: 0; padding: 0; }
  html, body {
    width: 1200px; height: 1200px; overflow: hidden;
    background: var(--backdrop);
    font-family: "Open Sans", Arial, sans-serif;
  }
  .canvas { position: relative; width: 1200px; height: 1200px; }

  .card {
    position: absolute; left: 300px; width: 592px; height: 350px;
    border-radius: 20px; overflow: hidden;
  }

  /* Back side */
  .card-back { top: 196px; background: var(--card-light); }
  .card-back .brand-band {
    position: absolute; inset: 0 0 auto 0; height: 210px;
    background: var(--card-dark);
    display: flex; align-items: center; justify-content: center;
  }
  .card-back .brand-name {
    color: var(--ink-deep); font-weight: 700; font-size: 50px;
    letter-spacing: 1px; text-transform: uppercase;
  }
  .note-lines { position: absolute; left: 35px; right: 33px; top: 210px; }
  .note-line { position: absolute; left: 0; right: 0; height: 2px; background: var(--rule); }
  .note-line:nth-child(1) { top: 36px; }
  .note-line:nth-child(2) { top: 71px; }
  .note-line:nth-child(3) { top: 106px; }

  /* Front side */
  .card-front { top: 636px; background: var(--card-dark); }
  .card-front .brand-name {
    position: absolute; left: 36px; top: 40px;
    color: var(--brand-blue); font-weight: 700; font-size: 34px;
    text-transform: uppercase; letter-spacing: 0.5px;
  }
  .owner { position: absolute; left: 35px; top: 186px; }
  .owner-name { color: var(--brand-blue); font-weight: 700; font-size: 21px; line-height: 1.2; }
  .owner-role { color: var(--text-light); font-size: 16px; margin-top: 2px; }
  .contact-list { position: absolute; left: 35px; top: 254px; list-style: none; }
  .contact-list li {
    display: flex; align-items: center; gap: 13px;
    color: var(--text-light); font-size: 16px; height: 21px;
  }
  .contact-icon { width: 14px; height: 14px; flex: none; }
  .brush-art {
    position: absolute; left: 300px; top: 44px; width: 275px; height: 265px;
    border-radius: 50%;
    background: linear-gradient(150deg, var(--art-tone-a), var(--art-tone-b));
  }
</style>
</head>
<body>
<main class="canvas">
  <section class="card card-back" aria-label="Card back">
    <div class="brand-band">
      <span class="brand-name">Brisk Coatings</span>
    </div>
    <div class="note-lines">
      <span class="note-line"></span>
      <span class="note-line"></span>
      <span class="note-line"></span>
    </div>
  </section>

  <section class="card card-front" aria-label="Card front">
    <span class="brand-name">Brisk Coatings</span>

    <div class="owner">
      <p class="owner-name">Marco "MJ"</p>
      <p class="owner-role">Owner - Licensed &amp; Insured</p>
    </div>

    <ul class="contact-list">
      <li>
        <svg class="contact-icon" viewBox="0 0 16 16" aria-hidden="true">
          <path fill="var(--brand-blue)" d="M2 5c0-2 3-3 6-3s6 1 6 3v1h-3V5H5v1H2zM4 8l2-2h4l2 2v5H4zM8 8.5a2 2 0 1 0 0 4a2 2 0 1 0 0-4z"/>
        </svg>
        931-555-0142
      </li>
      <li>
        <svg class="contact-icon" viewBox="0 0 16 16" aria-hidden="true">
          <rect x="1" y="3" width="14" height="10" fill="var(--brand-blue)"/>
          <path d="M1 3l7 6 7-6M1 13l5-5M15 13l-5-5" fill="none" stroke="var(--card-dark)" stroke-width="1.2"/>
        </svg>
        hello@briskcoatingstn.com
      </li>
      <li>
        <svg class="contact-icon" viewBox="0 0 16 16" aria-hidden="true">
          <circle cx="8" cy="8" r="7" fill="var(--brand-blue)"/>
          <path d="M1 8h14M8 1v14M3 4.5h10M3 11.5h10M8 1c-4 4-4 10 0 14M8 1c4 4 4 10 0 14" fill="none" stroke="var(--card-dark)" stroke-width="0.9"/>
        </svg>
        www.briskcoatingstn.com
      </li>
    </ul>

    <div class="brush-art" role="img" aria-label="Illustration of a paintbrush with a blue handle over a grey paint stroke"></div>
  </section>
</main>
</body>
</html>
```